Local fast-growing company in the service sector

We are looking for a modern business card design, which should also appear on our letterheads

Target Market(s)

Private and industrial sectors

Contact Information for Business Card

Vorname Name
Kellberger Str. 18
72458 Hagenwald
Tel.: 07146-839214-0
Name@agentur-kvtl.de

Colors
9d9d9d
919191
aaaaaa

Requirements
Must have
• The logo (file) in silver

```html
<!DOCTYPE html>
<html lang="de">
<head>
<meta charset="utf-8">
<title>KVTL Visitenkarte</title>
<link rel="stylesheet" href="https://fonts.googleapis.com/css2?family=Open+Sans:wght@400;700&display=swap">
<style>
  :root {
    --page-bg: #e6e6e4;
    --card-light: #e3e4e4;
    --card-light-end: #cfd0d1;
    --band-dark: #5a5c60;
    --band-dark-end: #3e4044;
    --arrow-silver: #aaaaaa;
    --arrow-highlight: #d6d7d8;
    --logo-grey: #7b7d80;
    --name-colour: #cfd6df;
    --detail-colour: #c4c6c9;
    --icon-colour: #b9bbbe;
    --card-edge: #f4f4f4;
  }
  html, body {
    margin: 0;
    width: 1200px;
    height: 969px;
    overflow: hidden;
    background: var(--page-bg);
  }
  .business-card {
    position: absolute;
    left: 100px;
    top: 200px;
    width: 1000px;
    height: 568px;
    font-family: "Open Sans", sans-serif;
  }
  .business-card svg { display: block; }
  .logo-name { font-family: "Open Sans", sans-serif; font-weight: 700; font-size: 100px; fill: var(--logo-grey); letter-spacing: 2px; }
  .contact-name { font-weight: 700; font-size: 26px; fill: var(--name-colour); letter-spacing: 0.5px; }
  .contact-line { font-weight: 400; font-size: 22px; fill: var(--detail-colour); }
  .contact-icon { fill: var(--icon-colour); }
</style>
</head>
<body>
<div class="business-card">
  <svg width="1000" height="568" viewBox="0 0 1000 568" xmlns="http://www.w3.org/2000/svg">
    <defs>
      <linearGradient id="cardLight" x1="0" y1="0" x2="1" y2="1">
        <stop offset="0" stop-color="var(--card-light)"/>
        <stop offset="1" stop-color="var(--card-light-end)"/>
      </linearGradient>
      <linearGradient id="bandDark" x1="0" y1="0" x2="1" y2="1">
        <stop offset="0" stop-color="var(--band-dark)"/>
        <stop offset="1" stop-color="var(--band-dark-end)"/>
      </linearGradient>
    </defs>

    <!-- card base -->
    <rect class="card-base" x="0" y="0" width="1000" height="568" fill="url(#cardLight)" stroke="var(--card-edge)" stroke-width="2"/>

    <!-- dark diagonal band -->
    <polygon class="diagonal-band" points="828,0 1000,0 1000,568 422,568" fill="url(#bandDark)"/>

    <!-- rising arrow along the band edge -->
    <g class="rising-arrow">
      <polygon points="400,568 436,568 806,52 790,40" fill="var(--arrow-silver)"/>
      <polygon points="400,568 412,568 796,44 790,40" fill="var(--arrow-highlight)"/>
      <polygon points="838,10 764,30 818,70" fill="var(--arrow-silver)"/>
    </g>

    <!-- company name -->
    <g class="logo">
      <rect x="80" y="78" width="96" height="96" fill="var(--logo-grey)"/>
      <text class="logo-name" x="200" y="168">KVTL</text>
    </g>

    <!-- contact details -->
    <g class="contact" text-anchor="end">
      <text class="contact-name" x="948" y="331">JONAS WEBER</text>
      <text class="contact-line" x="948" y="379">Kellberger Str. 18</text>
      <text class="contact-line" x="948" y="411">72458 Hagenwald</text>
      <text class="contact-line" x="905" y="456">07146-839214-0</text>
      <text class="contact-line" x="905" y="488">Name@agentur-kvtl.de</text>
      <text class="contact-line" x="905" y="520">www.agentur-kvtl.de</text>
    </g>

    <!-- icons -->
    <g class="contact-icon">
      <path d="M926 440 h20 a3 3 0 0 1 3 3 v4 h-6 v-3 h-14 v3 h-6 v-4 a3 3 0 0 1 3 -3 z M928 449 h16 l3 8 h-22 z"/>
      <rect x="925" y="473" width="22" height="15" rx="1"/>
      <polyline points="925,474 936,482 947,474" fill="none" stroke="var(--band-dark)" stroke-width="1.6"/>
      <circle cx="936" cy="513" r="10"/>
      <ellipse cx="936" cy="513" rx="4" ry="10" fill="none" stroke="var(--band-dark)" stroke-width="1.4"/>
      <line x1="926" y1="513" x2="946" y2="513" stroke="var(--band-dark)" stroke-width="1.4"/>
    </g>
  </svg>
</div>
</body>
</html>
```